Media & Printing Company 6 Page Brochure with a Level Field Theme

We are a printing company that offers most media communication services such as design, web design, mobile app and of course printing. All the profits of the company are used to fund a Level Field Organisation called “Level Field”. We are looking for a 6 page brochure, flat size 630mm x 210mm fold down to 210mm x 210mm. The brochure needs to push the need for companies to use our service on a “Corporate Social Responsibility” basis with losing the site that we are printers and designers.

Looking for a clean design with impact. A file is attached which shows our logo and some copy to give you an idea of what we are.

```html
<!DOCTYPE html>
<html lang="en">
<head>
<meta charset="utf-8">
<title>Northgate Media Works – Brochure Spread</title>
<link rel="stylesheet" href="https://fonts.googleapis.com/css2?family=Open+Sans:wght@300;400;600&display=swap">
<style>
:root{
  --sky:#1aa6e6;
  --pink:#e5197e;
  --yellow:#ffec00;
  --ink:#222;
  --grey-band:#efefef;
  --grey-deep:#dcdcdc;
  --tag:#b9b9b9;
  --frame:#d6d6d6;
  --leaf:#3b9a47;
  --white:#fff;
}
*{margin:0;padding:0;box-sizing:border-box}
html,body{width:1200px;height:422px;overflow:hidden;background:var(--white)}
body{font-family:"Open Sans",Arial,sans-serif;color:var(--ink)}
.spread{position:relative;width:1200px;height:422px;background:var(--white)}
.frame{position:absolute;left:18px;top:18px;width:1164px;height:387px;border:1px solid var(--frame)}
.block{position:absolute}
.panel-about{left:18px;top:18px;width:387px;height:297px;background:var(--sky)}
.panel-web{left:405px;top:18px;width:388px;height:97px;background:var(--white)}
.panel-design{left:405px;top:115px;width:388px;height:105px;background:var(--grey-band)}
.panel-print{left:405px;top:220px;width:388px;height:95px;background:var(--grey-deep)}
.panel-digital{left:405px;top:315px;width:388px;height:90px;background:var(--pink)}
.panel-green{left:793px;top:18px;width:389px;height:297px;background:var(--yellow)}
.copy{position:absolute;font-size:6.5px;line-height:1.2;font-weight:400}
.copy.on-dark{color:var(--white)}
.headline{position:absolute;font-weight:300;white-space:nowrap}
.label{position:absolute;font-size:11px;font-weight:400;white-space:nowrap}
.art{position:absolute;border-radius:6px}

.about-title{left:45px;top:148px;font-size:28px;color:var(--white)}
.about-copy{left:228px;top:100px;width:170px;font-size:6.3px;line-height:1.15}
.clients-copy{left:45px;top:326px;width:250px;font-size:6.8px}
.client-figure{left:311px;top:288px;width:18px;height:30px;background:#1877b5;border-radius:4px 4px 0 0}
.clients-tag{position:absolute;left:300px;top:331px}

.web-art{left:425px;top:26px;width:60px;height:80px;background:linear-gradient(135deg,#e94d8a,#6cc6b2 50%,#333)}
.web-label{left:490px;top:76px}
.web-copy{left:534px;top:38px;width:245px}

.design-copy{left:434px;top:137px;width:205px}
.design-label{left:645px;top:162px}
.design-art{left:690px;top:140px;width:76px;height:62px;background:linear-gradient(120deg,#f08a2a,#f5b26b)}

.print-art{left:420px;top:232px;width:58px;height:78px;background:linear-gradient(160deg,#1aa6e6,#e5197e 45%,#ffec00 75%,#222)}
.print-label{left:484px;top:246px}
.print-copy{left:530px;top:232px;width:248px}

.digital-copy{left:433px;top:322px;width:200px}
.digital-label{left:636px;top:347px;color:var(--white)}
.digital-art{left:708px;top:320px;width:78px;height:76px;background:linear-gradient(140deg,#f7e6b0,#9bd1d4 50%,#6aa78c)}

.butterfly-art{left:842px;top:30px;width:86px;height:74px;background:linear-gradient(180deg,#3a3a3a,#5a5a5a)}
.green-title{left:930px;top:58px;font-size:27px;color:#333}
.print-mark{left:815px;top:132px;width:118px;height:124px;border-radius:50%;background:radial-gradient(circle,#f6a21d,#e5197e 55%,#1aa6e6 85%,var(--yellow))}
.talk-title{left:820px;top:262px;font-size:14px;color:var(--leaf)}
.green-copy{left:944px;top:128px;width:228px}

.alien-title{position:absolute;left:822px;top:323px;font-size:9px;font-weight:400}
.alien-copy{left:822px;top:336px;width:350px;font-size:6.8px}
</style>
</head>
<body>
<main class="spread">
  <div class="block panel-about"></div>
  <div class="block panel-web"></div>
  <div class="block panel-design"></div>
  <div class="block panel-print"></div>
  <div class="block panel-digital"></div>
  <div class="block panel-green"></div>
  <div class="frame"></div>

  <h1 class="headline about-title">Who are we?</h1>
  <p class="copy on-dark about-copy">We are an Australian owned and operated unique provider of design, print and web services since 1984. Northgate Media Works is also a renowned social enterprise supporting Level Field, defending human rights in the hardest places. We give support to the most vulnerable in our community through the work of Level Field. Our Social Responsibility: Level Field targets abuse of authority, especially for people in mental hospitals and prisons. It empowers the disadvantaged, standing beside them as a community witness and ensuring their involvement in social inclusion programs. iVoice, the world's first prisoner webpage and interactive email system aimed at empowering people in prisons and forensic hospitals. It brings them into the digital world, reducing the divide and social exclusion that currently exists. FAIR SAY is the only publication that informs people in prisons and hospitals of their rights and reports on current issues facing them. It is distributed to all prisons and hospitals as well as all judges and politicians by name in Australia and New Zealand. www.levelfield.org.au</p>

  <p class="copy clients-copy">We have the privilege of working with some of the most diverse companies in Australia. We don't take this lightly. Whatever the size or nature of your print project, we are here to help. Our clients engage us in all aspects of design, print &amp; web and provide concise and accurate quotations. We view our clients as partners and work closely with them to achieve results they can measure.</p>
  <div class="art client-figure" role="img" aria-label="Small figure of a client in a suit"></div>
  <svg class="clients-tag" width="105" height="24" viewBox="0 0 105 24">
    <polygon points="0,12 12,0 105,0 105,24 12,24" fill="var(--tag)"/>
    <text x="56" y="17" text-anchor="middle" font-family="Open Sans, Arial, sans-serif" font-size="14" font-weight="300" fill="#333">Our Clients</text>
  </svg>

  <div class="art web-art" role="img" aria-label="Figure releasing colourful butterflies"></div>
  <span class="label web-label">Web</span>
  <p class="copy web-copy">Your website is your virtual office, so believe us when we tell you that IMAGE IS EVERYTHING. It is important whether you're a small business just around the corner or a large organisation with outlets all over Australia.<br>A great website is imagery, functionality and presence. A great website translates to better business.<br><br>We know how to build great websites</p>

  <p class="copy design-copy">From cutting edge graphic design to complete company branding or rebranding, we give our customers solutions that surpass their expectations. Northgate Media Works offers you the talents of our team with the creativity and experience to deliver on your next project. Whether it is website development, illustrations, publications, eBooks, or creating a corporate identity we have the necessary skills.</p>
  <span class="label design-label">Design</span>
  <div class="art design-art" role="img" aria-label="Orange butterflies rising from a pencil tip"></div>

  <div class="art print-art" role="img" aria-label="Figure with cyan, magenta, yellow and black ribbons"></div>
  <span class="label print-label">Print</span>
  <p class="copy print-copy">Northgate Media Works is a leader in Clean Printing Technologies using environmentally friendly soy inks and best quality papers, with high recycled content where quality isn't compromised. You are in the hands of expert printing industry machinists. We have a complete range of sheetfed offset presses from small to larger A1-size. Our printing equipment and efficient processes mean we can do magazines, brochures and catalogues at competitive rates providing the highest quality standards. As an added touch Northgate can add those special effects such as embossing, foiling, stamping and die-cutting.</p>

  <p class="copy on-dark digital-copy">Digital Print is ideal for quick and small print traditional printing methods. We offer fast turn around times and a wide range of stocks from 90gsm to 350gsm paper, card or labels. Even if it's an individualised or personalised piece of work, there are no minimum order and no need to store vast quantities of stock.</p>
  <span class="label digital-label">Digital Print</span>
  <div class="art digital-art" role="img" aria-label="Pastel butterflies in flight"></div>

  <div class="art butterfly-art" role="img" aria-label="Dark butterfly silhouette"></div>
  <h2 class="headline green-title">Sustainability.....</h2>
  <div class="art print-mark" role="img" aria-label="Colourful fingerprint pattern"></div>
  <h2 class="headline talk-title">Let's talk printing...</h2>
  <p class="copy green-copy">We purchase our stock from Australian paper suppliers. All stocks are FCC or PWC certified. Recycled stock is readily available ranging from 10% to 100% FCC Certified Stock. The Forest Care Council (FCC) is an independent, non-governmental, not-for-profit organisation that provides standard setting, trademark assurance and certification services for companies interested in responsible forestry. PWC Certified Stock. The Programme for Woodland Certification (PWC) is an independent, non-profit, non-governmental organisation, founded in 1999 which promotes sustainably managed forests through independent third party certification. The PWC provides an assurance mechanism to purchasers of paper products that they are promoting the sustainable management of forests. Using FCC and PWC approved stock means that it is from forests that are managed to meet social, ecological and economical needs of present and future generations. With FCC / PWC approved paper you can be confident that you are not contributing to the destruction of the world's forests. Our Product Portfolio: Brochures, leaflets, annual reports, calendars, short-run books, letterheads, business cards, corporate stationery, menus... the list just goes on. But the bottom line is this. We recognize that the quality of your finished product is the most important consideration. Quality encapsulates your brand values and is integral in promoting your business.</p>

  <h3 class="alien-title">Is digital technology alien to you?</h3>
  <p class="copy alien-copy">Northgate Media Works specialise in professional and effective email marketing campaigns that are custom designed for your business. E-mail marketing is a form of direct marketing which uses electronic mail as a means of communicating commercial or fundraising messages to an audience. Its abbreviation is EDM...email direct marketing. EDM design, creative email marketing and email newsletter template design are just some of the specialist services offered by Northgate Media Works. Sending a targeted EDM message straight to a potential customer's inbox is a fantastic opportunity to capture their attention, deliver your message and provide them with a clear call to action.</p>
</main>
</body>
</html>
```